Mobile Friendly Lead Generation Landing Page

We are a web marketing company that specialized in web lead generation. Recently we have started buying media from mobile devices and we need a mobile interface(landing page) where we can collect user data in an effective manner.

Our current mobile landing page is:
http://www.tutorpath.example.com/lp13d/index.aspx?a=true&source=841356
Through this you can see what the steps/questions users need to answer to get matched to a school. We need the design for the whole process.

We are pretty open for design ideas and our goal is to make this mobile optimized landing page have the look and feel of an app...but not an app.
There are several questions in the process but we are open to changing the way they are presented. As in, you can have one question at a time or a few.
The goal is to make this EXTREMELY EASY for users to interact with.

One example that we have liked is:
http://learnvane.example/schools/57214-page1.lvne (please note that this opens only on mobile devices)

Some of these screenshots are attached.

Our web form looks like this:
http://www.tutorpath.example.com/lp88/index.aspx?a=true

```html
<!DOCTYPE html>
<html lang="en">
<head>
<meta charset="utf-8">
<title>TutorPathApp – Get matched</title>
<link rel="stylesheet" href="https://fonts.googleapis.com/css2?family=Roboto:wght@400;500;700&family=Roboto+Condensed:wght@700&display=swap">
<style>
  :root{
    --bg:#ececec;
    --screen:#ffffff;
    --orange:#f98b1e;
    --blue:#1a8fbf;
    --ribbon:#2ba3d9;
    --ribbon-dark:#1672ab;
    --ink-muted:#8e8e8e;
    --field-border:#d6d6d6;
    --field-text:#9a9a9a;
  }
  *{box-sizing:border-box;margin:0;padding:0}
  html,body{width:1200px;height:1000px;overflow:hidden;background:var(--bg);font-family:"Roboto",Arial,sans-serif}
  .canvas{position:relative;width:1200px;height:1000px}
  .screen{position:absolute;top:144px;width:364px;height:646px;background:var(--screen);box-shadow:1px 2px 4px rgba(0,0,0,.18)}
  .screen--step1{left:25px}
  .screen--step2{left:418px}
  .screen--contact{left:810px}

  .app-header{position:absolute;left:0;top:0;width:364px;height:70px;background:var(--orange);color:#fff}
  .brand{position:absolute;left:10px;top:0;height:70px;display:flex;align-items:center;gap:10px}
  .brand__mark{width:30px;height:30px;border-radius:50%;background:#fff}
  .brand__name{font-family:"Roboto Condensed",Arial,sans-serif;font-weight:700;font-size:28px;letter-spacing:-.3px}
  .progress{position:absolute;left:261px;top:0;width:103px;height:70px;border-left:2px solid #fff;text-align:center;padding-top:20px;line-height:1.1}
  .progress__label{font-size:15px}
  .progress__value{font-size:16px;font-weight:700}

  .ribbon{position:absolute;left:0;top:90px;width:364px;height:62px}
  .ribbon__text{position:absolute;left:43px;top:93px;width:234px;height:42px;line-height:42px;color:#fff;font-size:18px;text-align:center}
  .ribbon__text b{font-weight:700}

  .question{position:absolute;left:11px;top:165px;width:300px;font-size:17px;line-height:22px;color:var(--ink-muted)}
  .question__step{color:var(--blue);font-weight:700;margin-right:4px}

  .choice{position:absolute;width:168px;height:30px;background:var(--blue);color:#fff;font-size:17px;display:flex;align-items:center;justify-content:center;text-align:center;border-radius:2px}
  .choice--selected{background:var(--orange)}
  .choice--tall{height:60px;line-height:22px}

  .field{position:absolute;left:11px;width:343px;height:43px;border:1px solid var(--field-border);border-radius:4px;display:flex;align-items:center;padding-left:12px;gap:10px;color:var(--field-text);font-size:17px}
  .field svg{width:22px;height:22px}

  .info{position:absolute;left:11px;top:484px;width:343px;height:93px;background:var(--ribbon);border-radius:4px;color:#fff;padding:10px 12px;font-size:15.5px;line-height:17px}
  .info__title{font-weight:700;font-size:16px}
  .info__lock{position:absolute;right:14px;bottom:12px;width:22px;height:26px}

  .back{position:absolute;left:10px;top:591px;width:343px;height:43px;border:1px solid #7cc3e2;border-radius:4px;color:var(--blue);font-size:22px;font-weight:700;display:flex;align-items:center;justify-content:center}
</style>
</head>
<body>
<div class="canvas">

  <!-- Step 1 -->
  <section class="screen screen--step1">
    <header class="app-header">
      <div class="brand"><span class="brand__mark"></span><span class="brand__name">TutorPathApp</span></div>
      <div class="progress"><div class="progress__label">PROGRESS</div><div class="progress__value">0%</div></div>
    </header>
    <svg class="ribbon" viewBox="0 0 364 62" aria-hidden="true">
      <polygon points="12,15 52,15 52,58 12,58 22,36" fill="var(--ribbon-dark)"/>
      <polygon points="352,15 312,15 312,58 352,58 342,36" fill="var(--ribbon-dark)"/>
      <polygon points="43,45 52,58 52,45" fill="#0f5a88"/>
      <polygon points="320,45 312,58 312,45" fill="#0f5a88"/>
      <rect x="43" y="3" width="277" height="42" fill="var(--ribbon)"/>
      <circle cx="296" cy="24" r="9" fill="none" stroke="#fff" stroke-width="2"/>
      <path d="M296 18v6h5" fill="none" stroke="#fff" stroke-width="2"/>
    </svg>
    <div class="ribbon__text">Get matched in <b>2 minutes</b></div>
    <p class="question"><span class="question__step">1/10</span> Please select your field of interest from the following</p>
    <div class="choice" style="left:11px;top:222px">Art &amp; Design</div>
    <div class="choice" style="left:186px;top:222px">Liberal Arts</div>
    <div class="choice" style="left:11px;top:260px">Business</div>
    <div class="choice" style="left:186px;top:260px">Nursing</div>
    <div class="choice" style="left:11px;top:298px">Criminal Justice</div>
    <div class="choice" style="left:186px;top:298px">Political Science</div>
    <div class="choice" style="left:11px;top:336px">Education/Teaching</div>
    <div class="choice" style="left:186px;top:336px">Psychology</div>
    <div class="choice" style="left:11px;top:374px">Engineering</div>
    <div class="choice" style="left:186px;top:374px">Religious Studies</div>
    <div class="choice" style="left:11px;top:412px">Health Care</div>
    <div class="choice choice--selected" style="left:186px;top:412px">Science &amp; Math</div>
    <div class="choice" style="left:11px;top:450px">Art &amp; Design</div>
    <div class="choice" style="left:186px;top:450px">Liberal Arts</div>
    <div class="choice" style="left:11px;top:488px">Business</div>
    <div class="choice" style="left:186px;top:488px">Nursing</div>
    <div class="back">Back</div>
  </section>

  <!-- Step 2 -->
  <section class="screen screen--step2">
    <header class="app-header">
      <div class="brand"><span class="brand__mark"></span><span class="brand__name">TutorPathApp</span></div>
      <div class="progress"><div class="progress__label">PROGRESS</div><div class="progress__value">0%</div></div>
    </header>
    <svg class="ribbon" viewBox="0 0 364 62" aria-hidden="true">
      <polygon points="12,15 52,15 52,58 12,58 22,36" fill="var(--ribbon-dark)"/>
      <polygon points="352,15 312,15 312,58 352,58 342,36" fill="var(--ribbon-dark)"/>
      <polygon points="43,45 52,58 52,45" fill="#0f5a88"/>
      <polygon points="320,45 312,58 312,45" fill="#0f5a88"/>
      <rect x="43" y="3" width="277" height="42" fill="var(--ribbon)"/>
      <circle cx="296" cy="24" r="9" fill="none" stroke="#fff" stroke-width="2"/>
      <path d="M296 18v6h5" fill="none" stroke="#fff" stroke-width="2"/>
    </svg>
    <div class="ribbon__text">Get matched in <b>2 minutes</b></div>
    <p class="question"><span class="question__step">2/10</span> Please select your field of interest from the following</p>
    <div class="choice choice--tall choice--selected" style="left:12px;top:222px">Graphic Design<br>&amp; Multimedia</div>
    <div class="choice choice--tall" style="left:187px;top:222px">Web Development<br>&amp; Design</div>
    <div class="back">Back</div>
  </section>

  <!-- Contact details -->
  <section class="screen screen--contact">
    <header class="app-header">
      <div class="brand"><span class="brand__mark"></span><span class="brand__name">TutorPathApp</span></div>
      <div class="progress"><div class="progress__label">PROGRESS</div><div class="progress__value">20%</div></div>
    </header>
    <svg class="ribbon" viewBox="0 0 364 62" aria-hidden="true">
      <polygon points="12,15 52,15 52,58 12,58 22,36" fill="var(--ribbon-dark)"/>
      <polygon points="352,15 312,15 312,58 352,58 342,36" fill="var(--ribbon-dark)"/>
      <polygon points="43,45 52,58 52,45" fill="#0f5a88"/>
      <polygon points="320,45 312,58 312,45" fill="#0f5a88"/>
      <rect x="43" y="3" width="277" height="42" fill="var(--ribbon)"/>
      <circle cx="296" cy="24" r="9" fill="none" stroke="#fff" stroke-width="2"/>
      <path d="M296 18v6h5" fill="none" stroke="#fff" stroke-width="2"/>
    </svg>
    <div class="ribbon__text">Get matched in <b>2 minutes</b></div>
    <p class="question"><span class="question__step">10/10</span></p>
    <div class="field" style="top:199px"><svg viewBox="0 0 22 22" aria-hidden="true"><path d="M3 19l1.5-5L15 3.5l3.5 3.5L8 17.5z" fill="#dcdcdc"/></svg>Salutation</div>
    <div class="field" style="top:255px"><svg viewBox="0 0 22 22" aria-hidden="true"><path d="M3 19l1.5-5L15 3.5l3.5 3.5L8 17.5z" fill="#dcdcdc"/></svg>First Name</div>
    <div class="field" style="top:312px"><svg viewBox="0 0 22 22" aria-hidden="true"><path d="M3 19l1.5-5L15 3.5l3.5 3.5L8 17.5z" fill="#dcdcdc"/></svg>Last Name</div>
    <div class="field" style="top:368px"><svg viewBox="0 0 22 22" aria-hidden="true"><path d="M3 19l1.5-5L15 3.5l3.5 3.5L8 17.5z" fill="#dcdcdc"/></svg>Email</div>
    <div class="field" style="top:425px"><svg viewBox="0 0 22 22" aria-hidden="true"><path d="M3 19l1.5-5L15 3.5l3.5 3.5L8 17.5z" fill="#dcdcdc"/></svg>Phone</div>
    <div class="info">
      <div class="info__title">Why Do we need this info?</div>
      We need this info beacause of sample text,sample text, sample text, sample text, sample text, sample text,
      <svg class="info__lock" viewBox="0 0 22 26" aria-hidden="true"><path d="M6 11V7a5 5 0 0 1 10 0v4" fill="none" stroke="#fff" stroke-width="2.5"/><rect x="2" y="11" width="18" height="14" rx="1" fill="#fff"/><rect x="10" y="15" width="2" height="5" fill="var(--ribbon)"/></svg>
    </div>
    <div class="back">Back</div>
  </section>

</div>
</body>
</html>
```